Business card for medical clinic

I need an upmarket, modern medical/health business card for my clinic

Contact Information for Business Card

name, address, email, qr code

```html
<!DOCTYPE html>
<html lang="en">
<head>
<meta charset="utf-8">
<title>Meridian Care Clinic – Business Card</title>
<link href="https://fonts.googleapis.com/css2?family=Crimson+Text:wght@400;600;700&display=swap" rel="stylesheet">
<style>
  :root {
    --navy: #1b2a4a;
    --navy-mid: #24496b;
    --sky: #2494cc;
    --sky-light: #3aa6dc;
    --white: #ffffff;
    --paper: #f4f5f6;
    --stage: #e9e6e1;
  }
  * { margin: 0; padding: 0; box-sizing: border-box; }
  html, body { width: 1200px; height: 900px; overflow: hidden; }
  body {
    background: var(--stage);
    font-family: "Crimson Text", Georgia, serif;
    position: relative;
  }
  .card {
    position: absolute;
    width: 600px;
    height: 343px;
    overflow: hidden;
    box-shadow: 0 6px 18px rgba(0,0,0,0.18);
  }

  /* Front */
  .card-front {
    left: 80px; top: 70px;
    background: linear-gradient(35deg, var(--sky) 0%, var(--navy-mid) 45%, var(--navy) 100%);
  }
  .brand-name {
    font-weight: 600;
    white-space: nowrap;
    letter-spacing: 0.5px;
  }
  .front-brand {
    position: absolute;
    left: 0; right: 0; top: 50%;
    transform: translateY(-50%);
    text-align: center;
    font-size: 38px;
    color: #17294a;
  }

  /* Back */
  .card-back {
    left: 520px; top: 487px;
    background: linear-gradient(100deg, #e4e5e7 0%, var(--white) 60%, var(--paper) 100%);
  }
  .back-brand {
    position: absolute;
    right: 44px; top: 52px;
    font-size: 28px;
    color: var(--navy);
  }
  .contact-band {
    position: absolute;
    left: 0; right: 0; bottom: 0;
    height: 128px;
    background: linear-gradient(20deg, var(--navy) 0%, var(--navy-mid) 55%, #2a88bf 100%);
  }
  .holder {
    position: absolute; left: 40px; top: 14px;
    color: var(--white);
  }
  .holder-name {
    font-weight: 700; font-size: 20px; letter-spacing: 0.5px;
    color: var(--sky-light); text-transform: uppercase; line-height: 1.1;
  }
  .holder-role { font-size: 15px; line-height: 1.1; }
  .contact-list {
    list-style: none;
    position: absolute; left: 56px; top: 62px;
    color: var(--white); font-size: 14px; line-height: 18px;
  }
  .contact-list li { display: flex; align-items: center; gap: 8px; }
  .contact-list svg { width: 13px; height: 13px; flex: none; }
  .divider {
    position: absolute; left: 345px; top: 60px;
    width: 1px; height: 52px; background: var(--sky-light);
  }
  .address {
    position: absolute; left: 360px; top: 66px;
    color: var(--white); font-size: 14px; line-height: 18px;
    font-style: normal;
  }
</style>
</head>
<body>

  <section class="card card-front" aria-label="Card front">
    <p class="brand-name front-brand">Meridian Care Clinic</p>
  </section>

  <section class="card card-back" aria-label="Card back">
    <p class="brand-name back-brand">Meridian Care Clinic</p>

    <div class="contact-band">
      <div class="holder">
        <p class="holder-name">Daniel Reyes</p>
        <p class="holder-role">Director</p>
      </div>

      <ul class="contact-list">
        <li>
          <svg viewBox="0 0 24 24" aria-hidden="true"><path fill="#3aa6dc" d="M6.6 10.8a15 15 0 0 0 6.6 6.6l2.2-2.2c.3-.3.7-.4 1-.2 1.1.4 2.3.6 3.6.6.6 0 1 .4 1 1V20c0 .6-.4 1-1 1A17 17 0 0 1 3 4c0-.6.4-1 1-1h3.5c.6 0 1 .4 1 1 0 1.3.2 2.5.6 3.6.1.3 0 .7-.2 1z"/></svg>
          <span>300-555-0142</span>
        </li>
        <li>
          <svg viewBox="0 0 24 24" aria-hidden="true"><rect x="2" y="5" width="20" height="14" rx="1" fill="#3aa6dc"/><path d="M2 6l10 7 10-7" fill="none" stroke="#1b2a4a" stroke-width="2"/></svg>
          <span>info@meridiancareclinic.com</span>
        </li>
        <li>
          <svg viewBox="0 0 24 24" aria-hidden="true"><g fill="none" stroke="#3aa6dc" stroke-width="2"><circle cx="12" cy="12" r="9"/><path d="M3 12h18M12 3v18"/></g></svg>
          <span>www.meridiancareclinic.com</span>
        </li>
      </ul>

      <span class="divider"></span>
      <address class="address">00 dummy city<br>dummy place 0000</address>
    </div>
  </section>

</body>
</html>
```